Vindgerdi - Start-up company selling electricity

Hello let me tell you about Vindgerdi.

Vindgerdi is start-up company selling electricity in Iceland. The operations of the company consist of making power usage forecasts for our customers, purchasing the electricity wholesale from the energy producers, and selling the electricity to the consumer. We are focused on tech by using optimization and machine learning to minimize electricity prices to our customers. Our marketing strategy is to portray a tech company mindset and to show dedication to driving down the electricity price on the market.

We need your help to make our website pop. Possible concepts to work with are as follows:

- Iceland the land of ice and fire
- Green energy
- Innovation
- Tech and data science

Link to our website: https://prufa.vindgerdi-example.is/
We are open to ideas.
Thank you!

Target Market(s)

Electricity consumers both homes and companies.

Number of Pages Required

1 page

Font styles to use
Serif
Sans Serif

```html
<!DOCTYPE html>
<html lang="en">
<head>
<meta charset="utf-8">
<title>Vindgerdi – Same electricity, just cheaper</title>
<link href="https://fonts.googleapis.com/css2?family=Oswald:wght@300;400;600;700&family=Lato:wght@400;700&family=IBM+Plex+Sans:wght@400;600&family=Inter:wght@700&display=swap" rel="stylesheet">
<style>
:root{
  --green:#4f9d12;
  --green-dark:#3f8a0c;
  --green-light:#8fdc16;
  --band:#e2efd6;
  --text:#3a3a3a;
  --muted:#666;
  --white:#fff;
}
*{margin:0;padding:0;box-sizing:border-box}
html,body{width:1200px;height:3384px;overflow:hidden}
body{position:relative;background:var(--white);font-family:'Lato',sans-serif;color:var(--text)}
.abs{position:absolute}
.center{left:0;width:1200px;text-align:center}

.brand{font-family:'Oswald',sans-serif;font-weight:700;color:var(--green);letter-spacing:1px;display:flex;align-items:center;gap:12px}
.brand-dot{width:44px;height:44px;border-radius:50%;background:var(--green)}
.header-brand{left:109px;top:30px;font-size:34px}

.main-nav{display:flex;gap:29px;font-family:'Inter',sans-serif;font-weight:700;font-size:13px;color:#111;text-transform:uppercase}
.header-nav{left:431px;top:49px}

.hero-art{left:0;top:116px;width:1200px;height:660px;background:linear-gradient(180deg,#f4f6f3 0%,#e4ece0 40%,#c9d8c1 70%,#9bb78a 100%)}
.hero-title{top:166px;font-family:'Oswald',sans-serif;font-weight:700;font-size:56px;color:var(--green);letter-spacing:1px}
.hero-text{top:244px;font-size:15px;line-height:30px;color:#555}

.btn{display:flex;align-items:center;justify-content:center;height:49px;border-radius:25px;background:linear-gradient(180deg,var(--green-light),var(--green));border-bottom:4px solid #2f6d08;color:var(--white);font-family:'Oswald',sans-serif;font-weight:600;font-size:18px;text-transform:uppercase}
.btn-hero{left:503px;top:322px;width:194px}
.btn-company{left:503px;top:1130px;width:194px}

.section-title{font-family:'Oswald',sans-serif;font-weight:700;font-size:38px;color:var(--green);text-transform:uppercase;line-height:1}
.title-rule{height:2px;background:var(--green)}
.welcome-title{top:852px}
.welcome-text{left:184px;top:934px;width:832px;text-align:center;font-size:17px;line-height:30px;color:#333}

.pricing-title{top:1400px}
.plan{top:1511px;width:469px;height:338px;background:var(--white);border:1px solid #ccc;box-shadow:0 2px 6px rgba(0,0,0,.25)}
.plan-1{left:120px}.plan-2{left:612px}
.plan-head{position:absolute;left:0;top:0}
.plan-name{position:absolute;left:0;top:22px;width:100%;text-align:center;font-family:'IBM Plex Sans',sans-serif;font-weight:600;font-size:17px;color:var(--white)}
.plan-price{position:absolute;left:0;top:56px;width:100%;text-align:center;font-family:'Oswald',sans-serif;font-weight:600;font-size:38px;color:var(--white)}
.plan-price small{font-size:9px;font-weight:400;margin-left:6px}
.plan-text{position:absolute;left:30px;top:154px;width:409px;text-align:center;font-size:15px;line-height:30px;color:var(--muted)}
.btn-plan{top:1824px;width:192px;height:46px}
.btn-plan-1{left:258px}.btn-plan-2{left:750px}
.price-link{top:1936px;font-family:'Oswald',sans-serif;font-weight:600;font-size:18px;color:var(--green);text-decoration:underline}

.faq-title{top:2170px}
.faq{left:198px;width:804px}
.faq-item{border:2px solid #d4d4d4;border-radius:3px;height:60px;display:flex;align-items:center;justify-content:space-between;padding:0 18px;font-family:'Oswald',sans-serif;font-weight:300;font-size:19px;color:#222;margin-bottom:11px;background:var(--white)}
.faq-item.open{color:var(--green);border-color:#bbb;margin-bottom:0}
.faq-answer{height:95px;border:1px solid #ddd;border-top:none;padding:24px 18px;font-size:17px;color:var(--muted);margin-bottom:0}
.caret{width:0;height:0;border-left:6px solid transparent;border-right:6px solid transparent;border-top:7px solid #222}
.open .caret{border-top:none;border-bottom:7px solid var(--green)}

.footer-art{left:0;top:2860px;width:1200px;height:524px;background:linear-gradient(180deg,#f7f9f5 0%,#eef3ea 60%,#dfe9d8 100%)}
.footer-brand{left:0;top:2990px;width:1200px;justify-content:center;font-size:52px}
.footer-brand .brand-dot{width:70px;height:70px}
.footer-nav{left:271px;top:3116px}
.contact{top:3177px;display:flex;gap:18px}
.contact-icon{width:72px;height:72px;border-radius:50%;border:2px solid var(--green);background:rgba(255,255,255,.6);display:flex;align-items:center;justify-content:center;margin-top:0}
.contact-label{font-family:'Oswald',sans-serif;font-weight:600;font-size:18px;color:var(--green);text-transform:uppercase}
.contact-value{font-family:'IBM Plex Sans',sans-serif;font-size:16px;line-height:30px;color:#222;letter-spacing:.5px}
.contact-loc{left:155px}
.contact-phone{left:494px;top:3177px}
.contact-phone .contact-info,.contact-mail .contact-info{padding-top:12px}
.contact-mail{left:763px}
.footer-rule{left:0;top:3306px;width:1200px;height:2px;background:var(--green)}
.copyright{top:3325px;font-family:'Oswald',sans-serif;font-weight:600;font-size:13px;color:var(--green)}
</style>
</head>
<body>

<div class="abs hero-art" role="img" aria-label="Light bulb holding wind turbines, a tree and a small city, set against a misty Icelandic valley"></div>
<div class="abs footer-art" role="img" aria-label="Faint field of wind turbines in a green landscape"></div>

<svg class="abs" style="left:0;top:0" width="1200" height="3384" viewBox="0 0 1200 3384" aria-hidden="true">
  <path d="M0 677 Q600 847 1200 677 L1200 790 L0 790Z" fill="#fff"/>
  <path d="M0 677 Q600 847 1200 677" fill="none" stroke="#4f9d12" stroke-width="5"/>
  <path d="M0 1386 Q600 1164 1200 1386 L1200 1991 Q600 2149 0 1991Z" fill="#e2efd6"/>
  <path d="M0 1386 Q600 1164 1200 1386" fill="none" stroke="#4f9d12" stroke-width="5"/>
  <path d="M1200 1991 Q600 2149 0 1991" fill="none" stroke="#4f9d12" stroke-width="5"/>
  <path d="M0 2850 L1200 2850 L1200 2990 Q600 2766 0 2990Z" fill="#fff"/>
  <path d="M0 2990 Q600 2766 1200 2990" fill="none" stroke="#4f9d12" stroke-width="5"/>
</svg>

<header>
  <div class="abs brand header-brand"><span class="brand-dot"></span>VINDGERDI</div>
  <nav class="abs main-nav header-nav"><span>Home</span><span>Terms of Business</span><span>Question &amp; Answer</span><span>About Vindgerdi</span><span>Contact Us</span></nav>
</header>

<section class="hero">
  <h1 class="abs center hero-title">SAME ELECTRICITY ~ JUST CHEAPER!</h1>
  <p class="abs center hero-text">Let's make the electricity system smarter together. Vindgerdi uses artificial intelligence, data science<br>and automation to minimize costs and promote eccentricity</p>
  <div class="abs btn btn-hero">Get Started</div>
</section>

<section class="welcome">
  <h2 class="abs center section-title welcome-title">Welcome to Vindgerdi</h2>
  <div class="abs title-rule" style="left:420px;top:901px;width:380px"></div>
  <p class="abs welcome-text">Vindgerdi's goal is to offer its customers the most favorable electricity prices in Iceland. Electricity is part of the monthly costs of households and companies, and by doing business with Vindgerdi, savings can be achieved and operating costs reduced. Vindgerdi wants to make the electricity system "smarter". Data science and the use of artificial intelligence can maximize the efficiency of the electricity system, minimize electricity costs and promote energy balance. Therefore, it can be said that by trading with Vindgerdi, you support the development of the Icelandic electricity market.</p>
  <div class="abs btn btn-company">Company</div>
</section>

<section class="pricing">
  <h2 class="abs center section-title pricing-title">Our Pricing Plan</h2>
  <div class="abs title-rule" style="left:465px;top:1449px;width:300px"></div>

  <article class="abs plan plan-1">
    <svg class="plan-head" width="469" height="135" viewBox="0 0 469 135" aria-hidden="true">
      <defs><linearGradient id="pg1" x1="0" x2="1"><stop offset="0" stop-color="#8fdc16"/><stop offset="1" stop-color="#4f9d12"/></linearGradient></defs>
      <path d="M0 0 H469 V78 Q234.5 178 0 78Z" fill="url(#pg1)"/>
    </svg>
    <div class="plan-name">ELECTRIC ACCELERATION</div>
    <div class="plan-price">6.95<small>ISK / KWH</small></div>
    <p class="plan-text">Lorem ipsum dolor sit amet, consectetur adipiscing elit, sed do eiusmod tempor incididunt ut labore et dolore magna aliqua. Ut enim ad minim veniam, quis nostrud exercitation ullamco laboris nisi ut aliquip</p>
  </article>
  <article class="abs plan plan-2">
    <svg class="plan-head" width="469" height="135" viewBox="0 0 469 135" aria-hidden="true">
      <defs><linearGradient id="pg2" x1="0" x2="1"><stop offset="0" stop-color="#8fdc16"/><stop offset="1" stop-color="#4f9d12"/></linearGradient></defs>
      <path d="M0 0 H469 V78 Q234.5 178 0 78Z" fill="url(#pg2)"/>
    </svg>
    <div class="plan-name">ELECTRIC ACCELERATION</div>
    <div class="plan-price">6.22<small>ISK / KWH</small></div>
    <p class="plan-text">Lorem ipsum dolor sit amet, consectetur adipiscing elit, sed do eiusmod tempor incididunt ut labore et dolore magna aliqua. Ut enim ad minim veniam, quis nostrud exercitation ullamco laboris nisi ut aliquip</p>
  </article>
  <div class="abs btn btn-plan btn-plan-1">Buy Now</div>
  <div class="abs btn btn-plan btn-plan-2">Buy Now</div>
  <div class="abs center price-link">PRICE COMPARISON</div>
</section>

<section class="faq-section">
  <h2 class="abs center section-title faq-title">Frequently Asked Questions</h2>
  <div class="abs title-rule" style="left:395px;top:2219px;width:440px"></div>
  <div class="abs faq" style="top:2287px">
    <div class="faq-item open">Can anyone buy electricity from Vindgerdi?<span class="caret"></span></div>
    <div class="faq-answer">Yes! Everyone in Iceland can buy electricity from Vindgerdi.</div>
    <div class="faq-item">How do I buy electricity from Vindgerdi?<span class="caret"></span></div>
    <div class="faq-item">Does it cost to switch to Vindgerdi?<span class="caret"></span></div>
    <div class="faq-item">What happens after I sign up for a business?<span class="caret"></span></div>
    <div class="faq-item">The future with Vindgerdi?<span class="caret"></span></div>
    <div class="faq-item">How do I quit trading?<span class="caret"></span></div>
  </div>
</section>

<footer>
  <div class="abs brand footer-brand"><span class="brand-dot"></span>VINDGERDI</div>
  <nav class="abs main-nav footer-nav"><span>Home</span><span>Terms of Business</span><span>Question &amp; Answer</span><span>About Vindgerdi</span><span>Contact Us</span></nav>

  <div class="abs contact contact-loc">
    <div class="contact-icon"><svg width="30" height="34" viewBox="0 0 30 34" aria-hidden="true"><path d="M15 2a10 10 0 0 0-10 10c0 8 10 18 10 18s10-10 10-18A10 10 0 0 0 15 2z" fill="#4f9d12"/><circle cx="15" cy="12" r="4" fill="#fff"/></svg></div>
    <div class="contact-info"><div class="contact-label">Location</div><div class="contact-value">Ljósvegur 8-10 170<br>Nesbær</div></div>
  </div>
  <div class="abs contact contact-phone">
    <div class="contact-icon"><svg width="32" height="32" viewBox="0 0 24 24" aria-hidden="true"><path d="M6.6 10.8a15 15 0 0 0 6.6 6.6l2.2-2.2a1 1 0 0 1 1-.25 11.4 11.4 0 0 0 3.6.57 1 1 0 0 1 1 1V20a1 1 0 0 1-1 1A17 17 0 0 1 3 4a1 1 0 0 1 1-1h3.5a1 1 0 0 1 1 1c0 1.25.2 2.45.57 3.57a1 1 0 0 1-.25 1z" fill="#4f9d12"/></svg></div>
    <div class="contact-info"><div class="contact-label">Phone Number</div><div class="contact-value">555-0142</div></div>
  </div>
  <div class="abs contact contact-mail">
    <div class="contact-icon"><svg width="34" height="26" viewBox="0 0 34 26" aria-hidden="true"><rect x="1" y="1" width="32" height="24" rx="2" fill="#4f9d12"/><path d="M2 3l15 11L32 3" fill="none" stroke="#fff" stroke-width="2"/></svg></div>
    <div class="contact-info"><div class="contact-label">Email Address</div><div class="contact-value">vindgerdi@vindgerdi-example.is</div></div>
  </div>

  <div class="abs footer-rule"></div>
  <div class="abs center copyright">© COPYRIGHTS 2021 VINDGERDI &nbsp;|&nbsp; ALL RIGHTS RESERVED</div>
</footer>

</body>
</html>
```